Website design for luxury private hair salon

I'm looking for someone to use my Logo and build me a website for my webpage www.corsetresses.com.au (You can have a look at it as it has every detail I need included on it already), however I want a fresh new appearance and it to look and feel super stylish.

I am thinking colours in black, with silver or white, beautiful hair images like the ones you'll see on the current webpage - the price list as per what you already see.

I will include a copy of my biz card on here, so you can see the feel of the card, and design a website with a similar feel. It is matt black with a foil silver.

Modern, but classic and fresh. I will also need you to be able to publish it to my URL for me as I have no idea how to do this. I need it up and running pronto!

The website will need to be able to be read clearly on all devices incluing smart phones and ipads. The URL is currently registered and hosted by Norvel Web

Thinking a Home Page - large logo etc and write up on who and what we offer
Services/Price List page - as per the price list on my current webpage
Contact Page - with a built in contact form.

Target Market(s)

Middle aged, fashionable, stylish women and men who enjoy luxury hair care and styling in an upmarket location.

Industry/Entity Type

Hair And Beauty

Number of Pages Required

3 page

Font styles to use
Other font styles liked:
• see my images for my current logo

Colors
000000
b2b2b2
a54499

Requirements
Must have
• Style
• Fast turnaround
• Be viewable on all devices, PC, ipads, smart phones
• Designer able to upload it so its a running website for me to my URL
Nice to have
• Just a really feminine, stylish website which is easy to read and shows some beautiful images of perfect hair
Should not have
• Browns, reds or orange colours.

```html
<!DOCTYPE html>
<html lang="en">
<head>
<meta charset="utf-8">
<title>Corsetresses Hair &amp; Body</title>
<link href="https://fonts.googleapis.com/css2?family=Noto+Serif:wght@400;700&family=Open+Sans:wght@400;600;700&display=swap" rel="stylesheet">
<style>
:root{
  --black:#000000;
  --ink:#111111;
  --silver:#b2b2b2;
  --plum:#a54499;
  --plum-dark:#7d2f74;
  --white:#ffffff;
  --text:#555555;
  --light:#f4f4f4;
}
*{box-sizing:border-box;margin:0;padding:0}
html,body{width:1200px;height:3640px;overflow:hidden}
body{font-family:"Open Sans",sans-serif;color:var(--text);background:var(--white);position:relative}
section,header,footer{position:absolute;left:0;width:1200px;overflow:hidden}

/* hero */
.hero{top:0;height:640px;background:var(--ink)}
.hero-photo{position:absolute;inset:0;background:
  radial-gradient(ellipse 380px 420px at 820px 420px,#b7825e 0%,#8a5a44 35%,rgba(60,40,36,0) 75%),
  radial-gradient(ellipse 300px 260px at 1050px 120px,#6b5a55 0%,rgba(40,34,36,0) 80%),
  linear-gradient(100deg,#141316 0%,#2a2729 35%,#3b3232 60%,#1f1b1d 100%)}
.hero-shade{position:absolute;inset:0;background:linear-gradient(180deg,rgba(0,0,0,.35),rgba(0,0,0,.1) 50%,rgba(0,0,0,.4))}
.nav{position:absolute;top:0;left:0;width:1200px;height:90px;display:flex;align-items:center;padding:0 80px}
.brand{font-family:"Noto Serif",serif;font-size:30px;color:var(--white);line-height:1}
.brand small{display:block;font-size:13px;margin-top:4px;letter-spacing:1px}
.menu{margin-left:auto;display:flex;gap:30px;align-items:center;list-style:none}
.menu li{color:var(--white);font-size:12px;font-weight:700;letter-spacing:1px}
.search{width:26px;height:26px;border:1px solid var(--white);border-radius:50%;display:flex;align-items:center;justify-content:center}
.hero-copy{position:absolute;top:290px;width:1200px;text-align:center;color:var(--white)}
.hero-copy h1{font-family:"Noto Serif",serif;font-size:48px;font-weight:700}
.hero-copy p{font-size:19px;margin-top:8px;letter-spacing:.5px}
.btn{display:inline-block;background:var(--plum);color:var(--white);font-size:12px;font-weight:700;letter-spacing:1px;padding:9px 20px;border-radius:3px}
.hero-copy .btn{margin-top:24px}
.dots{margin-top:16px;display:flex;gap:8px;justify-content:center}
.dots span{width:11px;height:11px;border:1px solid var(--white);border-radius:50%}
.dots span.on{background:var(--white)}

/* welcome */
.welcome{top:640px;height:570px;background:var(--white)}
.welcome-photo{position:absolute;left:0;top:0;width:570px;height:570px;background:
  radial-gradient(ellipse 260px 320px at 420px 160px,#d79ccd 0%,rgba(199,124,189,0) 75%),
  linear-gradient(135deg,#5a1d55,#a54499 55%,#c77cbd)}
.welcome-mark{position:absolute;left:140px;top:220px;color:var(--white);font-family:"Noto Serif",serif;font-size:62px;line-height:1}
.welcome-mark small{display:block;font-size:22px;margin:6px 0 0 120px}
.welcome-body{position:absolute;left:640px;top:70px;width:500px}
.welcome-body h2{font-family:"Noto Serif",serif;font-size:21px;color:var(--ink);letter-spacing:.5px;white-space:nowrap}
.welcome-body h2 em{font-style:normal;color:var(--plum)}
.rule{width:50px;height:3px;background:var(--plum);margin:14px 0 22px}
.welcome-body p{font-size:13px;line-height:1.75;margin-bottom:14px}
.products{position:absolute;left:640px;top:400px;width:520px;height:150px;background:linear-gradient(90deg,#f0eef2 0%,#d9cfe0 20%,#b98fc0 40%,#7fb6c8 58%,#d8a0cf 72%,#5b5560 88%,#ececec)}

/* services */
.services{top:1210px;height:500px;background:var(--white);text-align:center}
.section-title{font-family:"Noto Serif",serif;font-size:28px;color:var(--ink);letter-spacing:1px}
.services .section-title{margin-top:48px}
.center-rule{width:50px;height:3px;background:var(--plum);margin:14px auto 0}
.service-row{position:absolute;top:160px;left:110px;width:980px;display:flex;justify-content:space-between}
.service{width:220px}
.service-photo{width:170px;height:170px;border-radius:50%;margin:0 auto;border:5px solid var(--light);box-shadow:0 0 0 1px #ddd}
.service h3{font-family:"Noto Serif",serif;font-size:18px;color:var(--ink);margin-top:22px;font-weight:400}
.service p{font-size:12px;line-height:1.6;margin-top:10px;height:58px}
.more{display:inline-block;color:var(--plum);font-size:11px;font-weight:700;margin-top:14px;letter-spacing:.5px}
.arrow{position:absolute;top:230px}

/* price list */
.prices{top:1710px;height:500px;background:var(--black)}
.price-photo{position:absolute;left:540px;top:0;width:660px;height:500px;background:
  radial-gradient(ellipse 180px 220px at 360px 180px,#d9d9dc 0%,rgba(160,160,166,0) 80%),
  linear-gradient(180deg,rgba(0,0,0,0) 60%,#151517),
  linear-gradient(90deg,#000 0%,#38383b 25%,#8a8a90 50%,#55555a 75%,#2a2a2c)}
.price-panel{position:absolute;left:0;top:0;width:600px;height:500px;background:linear-gradient(90deg,#000 75%,rgba(0,0,0,0))}
.price-panel h2{position:absolute;left:80px;top:45px;font-family:"Noto Serif",serif;font-size:28px;color:var(--white);letter-spacing:1px}
.price-panel .rule{position:absolute;left:80px;top:92px;margin:0}
.price-table{position:absolute;left:80px;top:118px;width:420px;border-collapse:collapse;color:var(--white);font-size:12px}
.price-table th{font-size:10px;letter-spacing:1px;text-align:center;padding-bottom:8px}
.price-table td{padding:3.5px 0;border-bottom:1px solid #222}
.price-table td.num{text-align:center;width:100px;color:var(--silver)}

/* testimonials */
.testimonials{top:2210px;height:550px;background:var(--white);text-align:center}
.testimonials .section-title{margin-top:90px;font-size:30px}
.quote-row{position:absolute;top:240px;left:80px;width:1040px;display:flex;justify-content:space-between;text-align:left}
.quote{width:500px;display:flex;gap:28px;position:relative;padding-bottom:30px}
.avatar{flex:none;width:130px;height:130px;border-radius:50%}
.quote p{font-size:14px;line-height:1.8;font-style:italic}
.stars{color:var(--plum);font-size:15px;margin:14px 0 6px;letter-spacing:2px}
.quote cite{font-size:13px;font-style:normal;color:var(--ink);font-weight:600}
.quote-mark{position:absolute;right:0;bottom:-14px;font-family:"Noto Serif",serif;font-size:70px;color:#bbb;line-height:1}

/* contact */
.contact{top:2760px;height:480px;background:var(--plum)}
.contact-photo{position:absolute;left:0;top:0;width:600px;height:480px;background:
  radial-gradient(ellipse 170px 260px at 420px 200px,#e6d3b0 0%,#c9b08a 40%,rgba(150,140,120,0) 80%),
  linear-gradient(120deg,#3f4140,#77776e 35%,#a8a294 55%,#6f6a66 80%,#3a3a38)}
.contact-form{position:absolute;left:640px;top:34px;width:480px;color:var(--white)}
.contact-form h2{font-family:"Noto Serif",serif;font-size:26px;letter-spacing:1px}
.contact-form .rule{background:var(--white);margin:10px 0 20px}
.field{height:34px;background:var(--white);border-radius:2px;margin-bottom:10px;padding:0 12px;font-size:12px;color:#999;display:flex;align-items:center}
.intro{font-size:12px;margin:12px 0 6px;line-height:1.5}
.check{display:flex;gap:10px;font-size:11.5px;margin:6px 0;align-items:flex-start;line-height:1.4}
.check span.box{flex:none;width:13px;height:13px;border:1px solid var(--white);background:var(--white);margin-top:2px}
.submit{display:inline-block;margin-top:12px;border:1px solid var(--white);padding:7px 22px;font-size:12px;font-weight:700;letter-spacing:1px}

/* footer */
.footer{top:3240px;height:400px;background:var(--black);color:var(--silver)}
.foot-cols{position:absolute;top:70px;left:80px;width:1040px;display:flex;justify-content:space-between}
.foot-col h4{color:var(--white);font-size:13px;letter-spacing:1px;margin-bottom:18px}
.foot-col p,.foot-col li{font-size:12.5px;line-height:2;list-style:none}
.foot-col li::before{content:"› ";color:var(--plum)}
.foot-brand{font-family:"Noto Serif",serif;font-size:32px;color:var(--white);line-height:1;margin-bottom:18px}
.foot-brand small{display:block;font-size:13px;margin-top:4px}
.foot-input{width:220px;height:32px;background:var(--white);border-radius:2px;margin:14px 0 12px;font-size:11px;color:#999;padding:0 10px;display:flex;align-items:center}
.social li{display:flex;align-items:center;gap:10px;margin-bottom:8px}
.social li::before{content:none}
.social .dot{width:24px;height:24px;border:1px solid var(--silver);border-radius:50%}
.copyright{position:absolute;bottom:0;left:0;width:1200px;height:50px;border-top:1px solid #222;text-align:center;font-size:11px;line-height:50px;color:#888}
</style>
</head>
<body>

<header class="hero">
  <div class="hero-photo" role="img" aria-label="Photograph of a stylist curling a client's long glossy hair in the salon"></div>
  <div class="hero-shade"></div>
  <nav class="nav">
    <div class="brand">Corsetresses<small>Hair &amp; Body</small></div>
    <ul class="menu">
      <li>HOME</li><li>ABOUT US</li><li>SERVICE</li><li>PRICE</li><li>BLOG</li><li>CONTACT</li>
      <li class="search"><svg width="12" height="12" viewBox="0 0 12 12"><circle cx="5" cy="5" r="3.8" fill="none" stroke="#fff" stroke-width="1.5"/><line x1="8" y1="8" x2="11" y2="11" stroke="#fff" stroke-width="1.5"/></svg></li>
    </ul>
  </nav>
  <div class="hero-copy">
    <h1>Corsetresses Hair &amp; Body</h1>
    <p>We Are A Private Luxury Hair Salon In Australia</p>
    <span class="btn">MAKE AN APPOINTMENT</span>
    <div class="dots"><span class="on"></span><span></span><span></span></div>
  </div>
</header>

<section class="welcome">
  <div class="welcome-photo" role="img" aria-label="Purple toned photograph of flowing styled hair"></div>
  <div class="welcome-mark">Corsetresses<small>hair &amp; body</small></div>
  <div class="welcome-body">
    <h2>WELCOME TO <em>CORSETRESSES HAIR &amp; BODY</em></h2>
    <div class="rule"></div>
    <p>Our private salon offers a calm and elegant space where every guest receives unhurried, personal attention. We take time to understand your hair, your lifestyle and the look you love, then create a style that suits you.</p>
    <p>Using premium professional products and the latest techniques, our stylists deliver beautiful cuts, colour and finishing in a relaxed and luxurious setting.</p>
  </div>
  <div class="products" role="img" aria-label="Row of professional hair care product bottles"></div>
</section>

<section class="services">
  <h2 class="section-title">CORSETRESSES SERVICES</h2>
  <div class="center-rule"></div>
  <svg class="arrow" style="left:20px" width="20" height="36" viewBox="0 0 20 36"><polyline points="16,2 4,18 16,34" fill="none" stroke="#999" stroke-width="2"/></svg>
  <svg class="arrow" style="right:20px" width="20" height="36" viewBox="0 0 20 36"><polyline points="4,2 16,18 4,34" fill="none" stroke="#999" stroke-width="2"/></svg>
  <div class="service-row">
    <div class="service">
      <div class="service-photo" role="img" aria-label="Photograph of a fresh haircut and style" style="background:radial-gradient(circle at 60% 55%,#c08a66,#6b4a40 55%,#2b2427)"></div>
      <h3>Haircut &amp; Styling</h3>
      <p>Precision cuts and polished styling tailored to your face shape and daily routine.</p>
      <span class="more">READ MORE ▶</span>
    </div>
    <div class="service">
      <div class="service-photo" role="img" aria-label="Photograph of hair being coloured" style="background:radial-gradient(circle at 45% 40%,#d8d4cf,#8a8f96 50%,#2f3236)"></div>
      <h3>Colouring</h3>
      <p>Rich, lasting colour from soft tones to bold shades using gentle premium formulas.</p>
      <span class="more">READ MORE ▶</span>
    </div>
    <div class="service">
      <div class="service-photo" role="img" aria-label="Photograph of highlighted braided hair" style="background:radial-gradient(circle at 50% 50%,#e2c79a,#9c7a5a 50%,#3c3030)"></div>
      <h3>Highlighting</h3>
      <p>Natural sun kissed dimension with foils and balayage placed to flatter you.</p>
      <span class="more">READ MORE ▶</span>
    </div>
    <div class="service">
      <div class="service-photo" role="img" aria-label="Photograph of sleek straightened hair" style="background:radial-gradient(circle at 55% 45%,#e9d6b8,#b39472 50%,#4a3c38)"></div>
      <h3>Straightening</h3>
      <p>Smooth, frizz free results that last for weeks with treatments suited to your hair.</p>
      <span class="more">READ MORE ▶</span>
    </div>
  </div>
</section>

<section class="prices">
  <div class="price-photo" role="img" aria-label="Photograph of the salon interior with styling chairs and mirrors"></div>
  <div class="price-panel">
    <h2>PRICE LIST</h2>
    <div class="rule"></div>
    <table class="price-table">
      <tr><th></th><th>APPRENTICE</th><th>PRINCIPAL</th></tr>
      <tr><td>Styling</td><td class="num">35</td><td class="num">45</td></tr>
      <tr><td>Add Curls</td><td class="num">10</td><td class="num">15</td></tr>
      <tr><td>Style Up</td><td class="num">55</td><td class="num">75</td></tr>
      <tr><td>Ladies Cut</td><td class="num">40</td><td class="num">60</td></tr>
      <tr><td>Cut with Blow dry</td><td class="num">60</td><td class="num">85</td></tr>
      <tr><td>Restyle &amp; Finish</td><td class="num">70</td><td class="num">95</td></tr>
      <tr><td>Kids / Mens Cut</td><td class="num">25</td><td class="num">35</td></tr>
      <tr><td>Colour - Roots</td><td class="num">65</td><td class="num">85</td></tr>
      <tr><td>Colour Half Head</td><td class="num">90</td><td class="num">120</td></tr>
      <tr><td>Half Head Foils</td><td class="num">110</td><td class="num">140</td></tr>
      <tr><td>Full Head Foils</td><td class="num">150</td><td class="num">190</td></tr>
      <tr><td>Perm with Cut</td><td class="num">120</td><td class="num">150</td></tr>
      <tr><td>Permanent Straightening</td><td class="num">250</td><td class="num">320</td></tr>
    </table>
  </div>
</section>

<section class="testimonials">
  <h2 class="section-title">TESTIMONIALS</h2>
  <div class="center-rule"></div>
  <div class="quote-row">
    <div class="quote">
      <div class="avatar" role="img" aria-label="Portrait photograph of a client" style="background:radial-gradient(circle at 50% 45%,#c9a98a,#7a6458 55%,#3b3335)"></div>
      <div>
        <p>“ The team made me feel so welcome and relaxed. My colour has never looked better and I always leave feeling amazing and confident. ”</p>
        <div class="stars">★★★★★</div>
        <cite>Nina Carter - Corsetresses Hair &amp; Body</cite>
      </div>
      <span class="quote-mark">”</span>
    </div>
    <div class="quote">
      <div class="avatar" role="img" aria-label="Portrait photograph of a client" style="background:radial-gradient(circle at 50% 45%,#e6d2ae,#a68d6e 55%,#4a4040)"></div>
      <div>
        <p>“ A truly private and luxurious experience. Every visit is calm, personal and the results are always exactly what I asked for. ”</p>
        <div class="stars">★★★★★</div>
        <cite>Leah Morton - Corsetresses Hair &amp; Body</cite>
      </div>
      <span class="quote-mark">”</span>
    </div>
  </div>
</section>

<section class="contact">
  <div class="contact-photo" role="img" aria-label="Photograph of a woman with long blonde wavy hair outdoors"></div>
  <div class="contact-form">
    <h2>CONTACT US</h2>
    <div class="rule"></div>
    <div class="field">Name</div>
    <div class="field">Email Address</div>
    <div class="field">Phone No.</div>
    <div class="field">What can we help you with?</div>
    <p class="intro">Would you like to be contacted about any of the following? Tick all that apply below.</p>
    <div class="check"><span class="box"></span><span>Send me news about special offers and seasonal promotions</span></div>
    <div class="check"><span class="box"></span><span>Let me know about new services and product launches in the salon</span></div>
    <div class="check"><span class="box"></span><span>Please call me to book my next appointment</span></div>
    <span class="submit">SUBMIT</span>
  </div>
</section>

<footer class="footer">
  <div class="foot-cols">
    <div class="foot-col" style="width:260px">
      <div class="foot-brand">Corsetresses<small>Hair &amp; Body</small></div>
      <p>Shop 3, 12 Marlow Parade,<br>Brighton VIC 3186</p>
      <p>
        <svg width="11" height="11" viewBox="0 0 12 12"><path d="M2 1h3l1 3-2 1a7 7 0 0 0 3 3l1-2 3 1v3a1 1 0 0 1-1 1A10 10 0 0 1 1 2a1 1 0 0 1 1-1z" fill="#b2b2b2"/></svg>
        Phone: (03) 9555 0142</p>
      <p>
        <svg width="11" height="9" viewBox="0 0 12 9"><rect x=".5" y=".5" width="11" height="8" fill="none" stroke="#b2b2b2"/><polyline points=".5,.5 6,5 11.5,.5" fill="none" stroke="#b2b2b2"/></svg>
        Email: info@corsetresses.com.au</p>
    </div>
    <div class="foot-col">
      <h4>QUICK LINKS</h4>
      <ul><li>Home</li><li>About Us</li><li>Services</li><li>Price List</li><li>Blog</li><li>Contact</li></ul>
    </div>
    <div class="foot-col" style="width:260px">
      <h4>SIGN UP FOR NEWSLETTER</h4>
      <p>Join our mailing list for the latest offers and salon news.</p>
      <div class="foot-input">Enter Email</div>
      <span class="btn">SUBSCRIBE</span>
    </div>
    <div class="foot-col">
      <h4>SOCIAL</h4>
      <ul class="social">
        <li><span class="dot"></span>Community</li>
        <li><span class="dot"></span>Updates</li>
        <li><span class="dot"></span>Journal</li>
        <li><span class="dot"></span>Videos</li>
      </ul>
    </div>
  </div>
  <div class="copyright">2017 © Copyrights Corsetresses Hair &amp; Body All Rights Reserved</div>
</footer>

</body>
</html>
```